Business Card Design

Company is a Commercial Building Company specialising in New Construction and existing refurbishments

Industry/Entity Type

Business

Contact Information for Business Card

Liam Porter
Construction Manager
E Liam@marshbuilding.com.au
M 0400 213 594
Mail 14 Tarrant Rise Kerrow Bay WA 6299

```html
<!DOCTYPE html>
<html lang="en">
<head>
<meta charset="utf-8">
<title>Marsh Building &amp; Construction – Business Card</title>
<link rel="stylesheet" href="https://fonts.googleapis.com/css2?family=Open+Sans:ital,wght@0,400;0,600;0,700;1,400&display=swap">
<style>
  :root {
    --stage: #e9e6e1;
    --slate: #3d4859;
    --slate-shadow: #c9cacc;
    --paper: #f4f4f4;
    --cyan: #17a6cb;
    --ink: #3d4859;
    --body-ink: #4a5160;
    --white: #ffffff;
  }
  * { box-sizing: border-box; margin: 0; padding: 0; }
  html, body {
    width: 1200px; height: 804px; overflow: hidden;
    background: var(--stage);
    font-family: "Open Sans", Arial, sans-serif;
  }
  .canvas { position: relative; width: 1200px; height: 804px; }
  .card {
    position: absolute; top: 257px; width: 478px; height: 288px;
    overflow: hidden;
    box-shadow: 0 2px 6px rgba(0,0,0,0.25);
  }
  .card--front { left: 108px; background: var(--slate); }
  .card--back { left: 613px; background: var(--paper); }

  .brand { position: absolute; color: var(--white); font-weight: 600; line-height: 1.15; }
  .brand__mark { position: absolute; background: var(--cyan); }
  .brand__line { display: block; white-space: nowrap; }

  .card--front .brand { left: 148px; top: 176px; }
  .card--front .brand__line--main { font-size: 22px; }
  .card--front .brand__line--sub { font-size: 18px; }
  .card--front .brand__mark { left: 148px; top: 92px; width: 56px; height: 56px; }

  .back-panel { position: absolute; inset: 0; }
  .card--back .brand { left: 32px; top: 170px; }
  .card--back .brand__line--main { font-size: 17px; }
  .card--back .brand__line--sub { font-size: 14px; }
  .card--back .brand__mark { left: 32px; top: 96px; width: 44px; height: 44px; }

  .person { position: absolute; left: 244px; top: 57px; }
  .person__name {
    font-size: 19px; font-weight: 700; letter-spacing: 1.5px;
    color: var(--ink); text-transform: uppercase;
  }
  .person__role { font-size: 12.5px; font-style: italic; color: var(--cyan); margin-top: 2px; }

  .contact { position: absolute; left: 244px; top: 161px; list-style: none; font-size: 11.5px; color: var(--body-ink); }
  .contact__item { display: flex; align-items: center; height: 17px; white-space: nowrap; }
  .contact__icon { width: 10px; height: 10px; margin-right: 8px; fill: var(--cyan); }
  .contact__item--address { margin-top: 3px; }
</style>
</head>
<body>
<main class="canvas">
  <section class="card card--front" aria-label="Card front">
    <span class="brand__mark"></span>
    <div class="brand">
      <span class="brand__line brand__line--main">MARSH BUILDING</span>
      <span class="brand__line brand__line--sub">&amp; CONSTRUCTION</span>
    </div>
  </section>

  <section class="card card--back" aria-label="Card back">
    <svg class="back-panel" width="478" height="288" viewBox="0 0 478 288">
      <path fill="var(--slate-shadow)" d="M0 0 H214 C226 70 240 150 228 210 C222 245 214 270 210 288 H0 Z"/>
      <path fill="var(--slate)" d="M0 0 H205 C216 70 228 150 216 210 C210 245 204 270 200 288 H0 Z"/>
    </svg>
    <span class="brand__mark"></span>
    <div class="brand">
      <span class="brand__line brand__line--main">MARSH BUILDING</span>
      <span class="brand__line brand__line--sub">&amp; CONSTRUCTION</span>
    </div>

    <div class="person">
      <h1 class="person__name">Liam Porter</h1>
      <p class="person__role">Construction Manager</p>
    </div>

    <ul class="contact">
      <li class="contact__item">
        <svg class="contact__icon" viewBox="0 0 10 10"><path d="M2.5 0h5a1 1 0 0 1 1 1v8a1 1 0 0 1-1 1h-5a1 1 0 0 1-1-1V1a1 1 0 0 1 1-1zm0.5 1.5v6h4v-6z"/></svg>
        0400 213 594
      </li>
      <li class="contact__item">
        <svg class="contact__icon" viewBox="0 0 10 10"><path d="M0 2h10v1L5 6 0 3z M0 4l5 3 5-3v4H0z"/></svg>
        Liam@marshbuilding.com.au
      </li>
      <li class="contact__item">
        <svg class="contact__icon" viewBox="0 0 10 10"><circle cx="5" cy="5" r="4.3" fill="none" stroke="var(--cyan)" stroke-width="1.2"/><path d="M0.7 5h8.6M5 0.7v8.6" stroke="var(--cyan)" stroke-width="1"/></svg>
        www.marshbuilding.com.au
      </li>
      <li class="contact__item contact__item--address">14 Tarrant Rise Kerrow Bay WA 6299</li>
    </ul>
  </section>
</main>
</body>
</html>
```